Window company.

Hello,

We are a small family business located in Madrid, Spain that works nationwide to fix, change or mount the windows of your home / premises.

The group of possible clients to whom the flyer is focused ranges from 30 to 65 years, families in general who want comfort at home and extra savings every year in heating.

It must include not only graphics and a striking aesthetic in accordance with the concepts of wanting to reach / transmit the final product to the customer to sell the product.

Details to also include:

-Brief history of the company and its foundation in 2006. It will be subsequently translated into Spanish so put in words what you consider necessary so that the client stays with the concept that we are professionals.

--Specialized in exterior aluminum and PVC carpentry.

-We move to your home for a first visit and we provide the budget totally free without any commitment.

- Also payment facilities; up to 3 times, without interest.

-Contact details of the company. (WhatsApp, email, phone and location)
Open: Mon - Friday 11,00am - 9pm
Saturday: 12,00am - 7pm
Sunday: Closed

Also as a suggestion, to decide on your own, graphics of types of window openings, if you consider that anything that is striking for the client so it wonr be yet another advertising flyer.

We are open to all kinds of ideas, all of them involving marketing branding.

We are open to any type of idea and we want to stand out, the construction world is tough and we have an idea to grow, taking into account that it must not only be beautiful but commercial to attract potential customers with all kinds of purchasing power.

Thank you.

```html
<!DOCTYPE html>
<html lang="en">
<head>
<meta charset="utf-8">
<title>Ventara – Windows Flyer</title>
<link href="https://fonts.googleapis.com/css2?family=Fira+Sans:wght@600;700&family=Poppins:wght@300;400;500;600&family=Roboto:wght@400;700;900&display=swap" rel="stylesheet">
<style>
  :root{
    --red:#d01f41;
    --ink:#1f1f1f;
    --grey-text:#b1aca0;
    --white:#ffffff;
    --footer-dark:#161618;
    --footer-mid:#353537;
    --wall:#b7b4ae;
    --window:#f4f6f5;
    --chair:#3a4556;
    --floor:#9a6f45;
  }
  html,body{margin:0;padding:0;overflow:hidden;background:#e9e9e9;}
  .flyer{position:relative;width:848px;height:1200px;overflow:hidden;background:var(--white);font-family:"Poppins",sans-serif;color:var(--ink);}
  .interior-photo{position:absolute;left:0;top:110px;width:848px;height:600px;
    background:
      radial-gradient(ellipse 300px 120px at 470px 470px, rgba(58,69,86,.85), rgba(58,69,86,0) 100%),
      linear-gradient(180deg, rgba(154,111,69,0) 70%, rgba(154,111,69,.55) 100%),
      linear-gradient(90deg, var(--wall) 0%, #d8d6d1 22%, #c9cbcd 38%, #e7ebea 55%, var(--window) 78%, #e2e8e4 92%, #c8b295 100%);}
  .shapes{position:absolute;left:0;top:0;width:848px;height:1200px;}
  .brand-name{position:absolute;left:226px;top:96px;font-family:"Poppins",sans-serif;font-weight:600;font-size:31px;letter-spacing:1px;color:var(--grey-text);margin:0;}
  .quote-call{position:absolute;right:46px;top:28px;text-align:right;color:var(--red);}
  .quote-call p{margin:0;font-family:"Poppins",sans-serif;font-weight:300;font-size:27px;line-height:31px;}
  .quote-call .quote-phone{font-family:"Fira Sans",sans-serif;font-weight:700;font-size:28px;line-height:30px;}
  .offer-panel{position:absolute;left:62px;top:574px;width:357px;height:488px;background:var(--red);color:var(--white);
    clip-path:polygon(4px 0,100% 0,100% 100%,0 100%,0 28px);}
  .offer-title{position:absolute;left:32px;top:30px;margin:0;font-family:"Roboto",sans-serif;font-weight:900;font-size:26px;letter-spacing:-0.3px;}
  .offer-rule{position:absolute;left:32px;top:71px;width:276px;height:1px;background:var(--white);}
  .offer-list{position:absolute;left:45px;top:96px;width:272px;margin:0;padding:0;list-style:none;font-family:"Fira Sans",sans-serif;font-weight:600;font-size:23.5px;line-height:27.4px;letter-spacing:0.2px;}
  .offer-list li{position:relative;margin-bottom:28px;}
  .offer-list li::before{content:"";position:absolute;left:-11px;top:13px;width:3px;height:3px;border-radius:50%;background:var(--white);}
  .why-us{position:absolute;left:463px;top:692px;width:340px;}
  .why-title{display:flex;align-items:center;margin:0;font-family:"Roboto",sans-serif;font-weight:400;font-size:23px;}
  .why-title span{font-weight:700;}
  .why-title::after{content:"";flex:1;height:2px;background:#2a2a2a;margin-left:18px;}
  .why-text{margin:14px 0 0;width:326px;font-size:14.9px;line-height:19.3px;letter-spacing:0.7px;color:#2a2a2a;}
  .why-text + .why-text{margin-top:19px;}
  .opening-hours{position:absolute;left:463px;top:930px;display:flex;font-size:19.5px;line-height:30px;}
  .opening-label{font-family:"Poppins",sans-serif;margin-right:6px;}
  .opening-days{font-family:"Fira Sans",sans-serif;font-weight:600;color:var(--red);}
  .opening-days p{margin:0;}
  .site-footer{position:absolute;left:0;top:1062px;width:848px;height:138px;border-top:7px solid var(--red);box-sizing:border-box;
    background:linear-gradient(90deg,var(--footer-dark) 0%,var(--footer-mid) 55%,var(--footer-dark) 100%);color:var(--white);}
  .footer-pin{position:absolute;left:82px;top:45px;}
  .footer-address{position:absolute;left:131px;top:46px;width:300px;text-align:center;margin:0;font-family:"Poppins",sans-serif;font-weight:300;font-size:15.6px;line-height:23px;}
  .footer-phone-icon{position:absolute;left:514px;top:45px;}
  .footer-phone{position:absolute;left:570px;top:48px;margin:0;font-family:"Fira Sans",sans-serif;font-weight:700;font-size:28.5px;letter-spacing:0.3px;}
</style>
</head>
<body>
<div class="flyer">
  <div class="interior-photo" role="img" aria-label="Bright living and dining room with tall white framed windows, a glass round table and navy chairs"></div>

  <svg class="shapes" viewBox="0 0 848 1200" aria-hidden="true">
    <defs>
      <linearGradient id="steel" x1="0" y1="0" x2="1" y2="0">
        <stop offset="0" stop-color="#5c5c5c"/>
        <stop offset="0.5" stop-color="#d9d9d9"/>
        <stop offset="1" stop-color="#6a6a6a"/>
      </linearGradient>
    </defs>
    <path d="M0,0 H848 V100 Q416,284 0,160 Z" fill="#ffffff"/>
    <path d="M0,160 Q416,284 848,100 L848,108 Q416,292 0,170 Z" fill="url(#steel)"/>
    <path d="M0,168 Q416,290 848,106 L848,142 Q416,326 0,190 Z" fill="var(--red)"/>
    <path d="M400,574 Q640,585 848,625 L848,660 Q640,612 400,598 Z" fill="var(--red)"/>
    <path d="M400,598 Q640,612 848,660 L848,688 Q640,628 400,610 Z" fill="url(#steel)"/>
    <path d="M400,610 Q640,628 848,688 V1062 H400 Z" fill="#ffffff"/>
    <path d="M0,612 Q30,600 62,590 L62,642 Q30,658 0,678 Z" fill="var(--red)"/>
    <path d="M0,678 Q30,658 62,642 L62,655 Q30,670 0,690 Z" fill="url(#steel)"/>
    <path d="M0,690 Q30,670 62,655 V1062 H0 Z" fill="#ffffff"/>
  </svg>

  <p class="brand-name">VENTARA</p>

  <div class="quote-call">
    <p>Call us for free quote</p>
    <p class="quote-phone">+34 612 45 78 90</p>
  </div>

  <section class="offer-panel">
    <h2 class="offer-title">WHAT WE OFFER?</h2>
    <div class="offer-rule"></div>
    <ul class="offer-list">
      <li>Specialized in exterior aluminum and PVC carpentry.</li>
      <li>We move to your home for a first visit and we provide the budget totally free without any commitment.</li>
      <li>Also payment facilities; up to 3 times, without interest.</li>
    </ul>
  </section>

  <section class="why-us">
    <h2 class="why-title">WHY&nbsp;<span>US?</span></h2>
    <p class="why-text">We are a small family business located in Madrid, Spain that works nationwide to fix, change or mount the windows of your home / premises. We are founded in 2006.</p>
    <p class="why-text">We offer full service from initial contact to final fitting, making sure all projects are finsied to the highest standard.</p>
  </section>

  <div class="opening-hours">
    <span class="opening-label">Open:</span>
    <div class="opening-days">
      <p>Mon - Friday 11,00am - 9pm</p>
      <p>Saturday: 12,00am - 7pm</p>
      <p>Sunday: Closed</p>
    </div>
  </div>

  <footer class="site-footer">
    <svg class="footer-pin" width="31" height="46" viewBox="0 0 31 46" aria-hidden="true">
      <path d="M15.5 0C7 0 0 6.8 0 15.3 0 26 15.5 46 15.5 46S31 26 31 15.3C31 6.8 24 0 15.5 0Z" fill="var(--red)"/>
      <circle cx="15.5" cy="15" r="6" fill="#242426"/>
    </svg>
    <p class="footer-address">Pol. Ind. Ribera Norte<br>Getafe, Spain 28906</p>
    <svg class="footer-phone-icon" width="40" height="38" viewBox="0 0 40 38" aria-hidden="true">
      <path d="M6 4 L12 2 L16 11 L12 15 Q15 23 22 27 L26 23 L35 28 L33 34 Q30 38 24 36 Q8 30 3 12 Q2 6 6 4Z" fill="var(--red)"/>
      <path d="M22 3 Q32 4 35 14" stroke="var(--red)" stroke-width="2.5" fill="none" stroke-linecap="round"/>
      <path d="M21 9 Q27 10 29 16" stroke="var(--red)" stroke-width="2.5" fill="none" stroke-linecap="round"/>
    </svg>
    <p class="footer-phone">+34 612 45 78 90</p>
  </footer>
</div>
</body>
</html>
```